Web site for radio show

I've got a radio show starting on OrbitalWave and need a web site for it. I am familiar with SitePress, so I'd like to get a design for a SitePress-based web site for the show.

I'm also posting a logo project to be done at the same time.

The best radio show web site I've seen is the Cosmic Tuesday site (www.cosmictuesday-example.com). That's a good model but I don't want to start with that much complexity and content. The initial site that I'd like you to design would have the following parts:
- Upcoming shows
- Past shows (including links to authors, their web sites, and their books)
- Twitter feed
- Blog
- About
- ...and anything else you think would be necessary

For colors, I'd like it to be consistent with my personal web site: www.kellaway-ventures-example.com

Target Market(s)

The target market for this show is mid- to upper-level managers

Industry/Entity Type

Radio

Requirements
Must have
• The project has to proceed in (at least) two stages: a first rough layout, and a second finished design. Whether you want a third stage in between with look and feel options is up to you.

```html
<!DOCTYPE html>
<html lang="en">
<head>
<meta charset="utf-8">
<title>Kellaway Show</title>
<link rel="stylesheet" href="https://fonts.googleapis.com/css2?family=Open+Sans:ital,wght@0,400;0,600;0,700;1,400&display=swap">
<style>
:root{
  --red:#c30000;
  --red-dark:#9e0000;
  --red-soft:#b83a3a;
  --ink:#1a1a1a;
  --muted:#9a9a9a;
  --line:#dcdcdc;
  --band:#e8e8e8;
  --topbar:#f2f2f2;
  --footer:#0e0e0e;
  --tweet:#57a9d8;
}
*{box-sizing:border-box;margin:0;padding:0}
html,body{width:1200px;height:2711px;overflow:hidden;background:#fff}
body{font-family:"Open Sans",Arial,sans-serif;color:var(--ink);position:relative}

/* header */
.topbar{position:absolute;left:0;top:0;width:1200px;height:92px;background:var(--topbar)}
.brand{position:absolute;left:110px;top:30px;font-size:25px;letter-spacing:-.3px;color:var(--ink)}
.brand b{color:var(--red);font-weight:700}
.newsletter{position:absolute;left:447px;top:31px;font-size:11px;font-weight:700;line-height:13px}
.email{position:absolute;left:546px;top:22px;width:206px;height:46px;background:#fff;border:3px solid #e3e3e3;display:flex;align-items:center}
.email span{flex:1;padding-left:10px;font-size:13px;font-style:italic;color:#b5b5b5}
.email i{width:44px;height:40px;background:#efefef;display:flex;align-items:center;justify-content:center}
.social{position:absolute;left:876px;top:36px;display:flex;align-items:center}
.social span{width:18px;height:18px;border-radius:50%;background:#c8c8c8;margin:0 19px}
.social em{width:1px;height:20px;background:#d0d0d0}

.nav{position:absolute;left:0;top:92px;width:1200px;height:69px;background:var(--red)}
.nav a{position:absolute;top:0;height:69px;line-height:69px;color:#fff;font-size:14px;font-weight:700;text-decoration:none}
.nav a.active{background:var(--red-dark);padding:0 22px;left:110px}
.search{position:absolute;left:891px;top:110px;width:199px;height:30px;border-bottom:1px solid #e77;color:#f2a0a0;font-size:13px;font-style:italic;padding:4px 6px}
.search svg{position:absolute;right:6px;top:6px}

/* hero */
.hero{position:absolute;left:110px;top:202px;width:980px;height:400px;background:linear-gradient(120deg,#c9b9a4 0%,#8a7666 35%,#3e3a3a 60%,#6c7f93 85%,#a9b7c4 100%)}
.hero-caption{position:absolute;left:665px;top:421px;width:425px;height:181px;background:var(--red);color:#fff;padding:12px 22px}
.hero-caption h1{font-size:23px;font-weight:600;letter-spacing:-.2px;margin-bottom:8px}
.hero-caption p{font-size:10.5px;line-height:14.5px}
.dots{position:absolute;left:486px;top:588px;display:flex;gap:4px}
.dots i{width:6px;height:6px;border-radius:50%;background:#fff;opacity:.8}

/* section headings */
.band{position:absolute;left:110px;width:980px;height:42px;background:var(--band);border-left:5px solid var(--red);padding-left:18px;line-height:42px;color:var(--red);font-size:15px;font-weight:700}

/* cards */
.card{position:absolute}
.card .photo{width:100%}
.card h3{font-size:19px;font-weight:400;line-height:26px;margin-top:14px}
.card p{font-size:14.5px;line-height:22px;color:var(--muted);margin-top:18px}
.meta{font-size:10px;color:var(--muted);margin-top:16px;letter-spacing:.3px}
.meta b{color:var(--ink);font-weight:600}
.meta s{text-decoration:none;margin:0 10px}
.actions{border-top:1px solid var(--line);border-bottom:1px solid var(--line);height:42px;margin-top:14px;display:flex;justify-content:space-between;align-items:center;padding:0 8px}
.actions b{font-size:12px;font-weight:700}
.actions span{font-size:10px}

/* about */
.about{position:absolute;left:110px;top:1872px;width:476px;height:311px;border:2px solid var(--red-soft);overflow:hidden}
.about h2{background:var(--red-soft);color:#fff;font-size:16px;font-weight:700;height:43px;line-height:43px;padding-left:22px}
.about .photo{position:absolute;left:6px;top:70px;width:223px;height:230px;background:linear-gradient(180deg,#c7ccd0,#7d8590 60%,#3a3d44)}
.about p{position:absolute;left:236px;top:66px;width:232px;font-size:10.2px;line-height:15.4px;color:#666}

.tabs{position:absolute;left:616px;top:1874px;width:474px;height:51px;display:flex}
.tabs div{flex:1;color:#fff;font-size:12px;font-weight:700;padding-left:16px;line-height:51px}
.tabs .on{background:var(--red-soft)}
.tabs .off{background:#c94848}
.post{position:absolute;left:616px;display:flex;gap:20px}
.post .thumb{width:83px;height:54px}
.post h4{font-size:14px;font-weight:600;margin-top:4px}
.post small{font-size:9.5px;color:var(--muted);display:block;margin-top:10px}
.post small b{color:var(--ink);font-weight:600}

.rule{position:absolute;left:110px;top:2203px;width:980px;height:5px;background:var(--red)}

.tweets{position:absolute;left:0;top:2250px;width:1200px;text-align:center}
.tweets h2{font-size:13px;color:var(--red);font-weight:700}
.tweets .mark{width:54px;height:54px;border-radius:50%;background:var(--tweet);margin:24px auto 20px}
.tweets p{font-size:20px;font-style:italic;color:#9b9b9b;line-height:30px}
.tweets p a{color:#3a8cc4;text-decoration:none}
.tweets small{display:block;font-size:12px;font-weight:700;margin-top:18px}

.footer{position:absolute;left:0;top:2602px;width:1200px;height:109px;background:var(--footer);color:#fff}
.footer .links{position:absolute;left:110px;top:12px;font-size:11px;line-height:21px}
.partner{position:absolute;left:878px;top:18px;width:214px;height:58px;background:#fff;border:4px solid #dbe6f2;display:flex;align-items:center;justify-content:center;font-size:22px;font-weight:700;color:#1c4f9c}
</style>
</head>
<body>

<header class="topbar">
  <div class="brand"><b>KELLAWAY</b> SHOW</div>
  <div class="newsletter">NEWSLETTER<br>SUBSCRIBE</div>
  <div class="email"><span>Email ...</span><i><svg width="18" height="16" viewBox="0 0 18 16"><path d="M1 8 L17 1 L13 15 L8 10 Z" fill="#d51f1f"/></svg></i></div>
  <div class="social"><span></span><em></em><span></span><em></em><span></span><em></em><span></span></div>
</header>

<nav class="nav">
  <a class="active">HOME</a>
  <a style="left:224px">DESIGN</a>
  <a style="left:323px">POLITICS</a>
  <a style="left:435px">TRAVEL</a>
  <a style="left:535px">TECHNOLOGY</a>
  <a style="left:681px">SPORT</a>
  <a style="left:773px">PAGES</a>
</nav>
<div class="search">Search<svg width="16" height="16" viewBox="0 0 16 16"><circle cx="6.5" cy="6.5" r="4.5" fill="none" stroke="#f2a0a0" stroke-width="2"/><path d="M10 10 L14 14" stroke="#f2a0a0" stroke-width="2"/></svg></div>

<div class="hero" role="img" aria-label="Radio host in headphones and cap smiling at a studio microphone"></div>
<div class="hero-caption">
  <h1>WELCOME TO KELLAWAY SHOW</h1>
  <p>Lorem ipsum dolor sit amet, consectetuer adipiscing elit. Aenean commodo ligula eget dolor. Aenean massa. Cum sociis natoque penatibus et magnis dis parturient montes, nascetur ridiculus mus. Donec quam felis, ultricies nec, pellentesque eu, pretium quis, sem. Nulla consequat massa quis enim. Donec pede justo, fringilla vel, aliquet nec, vulputate eget, arcu. In enim justo, rhoncus ut, imperdiet a, venenatis vitae, justo. Nullam dictum felis eu pede mollis pretium. Integer tincidunt. Cras dapibus. Vivamus elementum semper</p>
</div>
<div class="dots"><i></i><i></i><i></i></div>

<div class="band" style="top:665px">UPCOMING SHOWS</div>

<article class="card" style="left:110px;top:748px;width:222px">
  <div class="photo" style="height:139px;background:linear-gradient(135deg,#5a1a9c,#c2248a 50%,#f0b020)" role="img" aria-label="Jazz show artwork with saxophone player"></div>
  <h3>Cras bibendug at ustorna ret Tre vivo trui lopull isdo</h3>
  <p>Lorem ipsum dolor sit amet, consectetur adipisicing elit, sed do eiusmod tempor incididunt ut labore et dolore magna aliqua.</p>
  <div class="meta">POSTED : <b>20 OCT</b><s>/</s><b>TRAVEL</b></div>
  <div class="actions"><b>READ MORE →</b><span>53 COMMENTS</span></div>
</article>
<article class="card" style="left:363px;top:748px;width:222px">
  <div class="photo" style="height:139px;background:linear-gradient(135deg,#8c8c8c,#d6cfc6 50%,#6b6b6b)" role="img" aria-label="Presenter with headphones at a studio microphone"></div>
  <h3>Cras bibendug at ustorna ret Tre vivo trui lopull isdo</h3>
  <p>Lorem ipsum dolor sit amet, consectetur adipisicing elit, sed do eiusmod tempor incididunt ut labore et dolore magna aliqua.</p>
  <div class="meta">POSTED : <b>20 OCT</b><s>/</s><b>TECHNOLOGY</b></div>
  <div class="actions"><b>READ MORE →</b><span>53 COMMENTS</span></div>
</article>
<article class="card" style="left:615px;top:748px;width:222px">
  <div class="photo" style="height:139px;background:linear-gradient(160deg,#1b3d7a,#2f6fb5 45%,#b08a6c)" role="img" aria-label="On-air studio scene with presenter"></div>
  <h3>Cras bibendug at ustorna ret Tre vivo trui lopull isdo</h3>
  <p>Lorem ipsum dolor sit amet, consectetur adipisicing elit, sed do eiusmod tempor incididunt ut labore et dolore magna aliqua.</p>
  <div class="meta">POSTED : <b>20 OCT</b><s>/</s><b>SPORT</b></div>
  <div class="actions"><b>READ MORE →</b><span>53 COMMENTS</span></div>
</article>
<article class="card" style="left:868px;top:748px;width:222px">
  <div class="photo" style="height:139px;background:linear-gradient(135deg,#d8d4cc,#6a5648 50%,#3e5b86)" role="img" aria-label="Laughing radio host in a cap and headphones"></div>
  <h3>Cras bibendug at ustorna ret Tre vivo trui lopull isdo</h3>
  <p>Lorem ipsum dolor sit amet, consectetur adipisicing elit, sed do eiusmod tempor incididunt ut labore et dolore magna aliqua.</p>
  <div class="meta">POSTED : <b>20 OCT</b><s>/</s><b>DESIGN</b></div>
  <div class="actions"><b>READ MORE →</b><span>53 COMMENTS</span></div>
</article>

<div class="band" style="top:1258px">PAST SHOWS</div>

<article class="card" style="left:110px;top:1341px;width:307px">
  <div class="photo" style="height:191px;background:linear-gradient(180deg,#3c5e48,#2a2a2a 55%,#9aa3a8)" role="img" aria-label="Studio mixing desk and microphone"></div>
  <h3>France, Italy see leeway on budget rules at EU summit</h3>
  <div class="meta">POSTED : <b>20 OCT</b><s>/</s><b>WORLD</b></div>
  <p>Lorem ipsum dolor sit amet, consectetur adipisicing elit, sed do eiusmod tempor incididunt ut labore et dolore magna aliqua.</p>
  <div class="actions"><b>READ MORE →</b><span>53 COMMENTS</span></div>
</article>
<article class="card" style="left:447px;top:1341px;width:307px">
  <div class="photo" style="height:191px;background:linear-gradient(135deg,#b9a692,#5a4a40 50%,#2a2a2c)" role="img" aria-label="Host speaking close to a studio microphone"></div>
  <h3>Halvorsen proposes increasing youth unemployment funds at EU summit</h3>
  <div class="meta">POSTED : <b>20 OCT</b><s>/</s><b>WORLD</b></div>
  <p>Lorem ipsum dolor sit amet, consectetur adipisicing elit, sed do eiusmod tempor incididunt ut labore et dolore magna aliqua.</p>
  <div class="actions"><b>READ MORE →</b><span>53 COMMENTS</span></div>
</article>
<article class="card" style="left:783px;top:1341px;width:307px">
  <div class="photo" style="height:191px;background:linear-gradient(135deg,#cfc6b8,#6e5a4c 45%,#4f6e96)" role="img" aria-label="Smiling host at a radio desk"></div>
  <h3>Adeyemi visits the Russian president Pavel Sorokin</h3>
  <div class="meta">POSTED : <b>20 OCT</b><s>/</s><b>WORLD</b></div>
  <p>Lorem ipsum dolor sit amet, consectetur adipisicing elit, sed do eiusmod tempor incididunt ut labore et dolore magna aliqua.</p>
  <div class="actions"><b>READ MORE →</b><span>53 COMMENTS</span></div>
</article>

<section class="about">
  <h2>ABOUT US</h2>
  <div class="photo" role="img" aria-label="Businesswoman in a dark suit standing in an office"></div>
  <p>Lorem ipsum dolor sit amet, consectetuer adipiscing elit. Aenean commodo ligula eget dolor. Aenean massa. Cum sociis natoque penatibus et magnis dis parturient montes, nascetur ridiculus mus. Donec quam felis, ultricies nec, pellentesque eu, pretium quis, sem. Nulla consequat massa quis enim. Donec pede justo, fringilla vel, aliquet nec, vulputate eget, arcu. In enim justo, rhoncus ut, imperdiet a, venenatis vitae, justo. Nullam dictum felis eu pede mollis pretium. Integer tincidunt. Cras dapibus. Vivamus elementum semper nisi. Aenean vulputate eleifend tellus. Aenean leo ligula, porttitor</p>
</section>

<div class="tabs"><div class="on">NEW POSTS</div><div class="off">POPULAR POSTS</div></div>
<div class="post" style="top:1946px"><div class="thumb" style="background:linear-gradient(135deg,#e9e4dc,#8a6d52)" role="img" aria-label="Tennis player on court"></div><div><h4>All the titles you need</h4><small>POSTED : <b>15 OCT</b></small></div></div>
<div class="post" style="top:2028px"><div class="thumb" style="background:linear-gradient(135deg,#2b2b35,#6f6a70)" role="img" aria-label="Rings emblem on a dark stage"></div><div><h4>The book that i love to read all the time</h4><small>POSTED : <b>15 OCT</b></small></div></div>
<div class="post" style="top:2111px"><div class="thumb" style="background:linear-gradient(135deg,#4a3a3a,#8a2a2a 50%,#3a4a6a)" role="img" aria-label="Team group photo"></div><div><h4>All the titles you need in your website</h4><small>POSTED : <b>15 OCT</b></small></div></div>

<div class="rule"></div>

<section class="tweets">
  <h2>LATEST TWEETS</h2>
  <div class="mark"></div>
  <p>How to embed CloudDocs (spreadsheets, documents, forms, etc.) into <a>#SitePress</a>. Read here<br><a>http://lnk.example/tkql2lcsxb</a></p>
  <small>55 SECONDS AGO</small>
</section>

<footer class="footer">
  <div class="links">Home | About | Listen | Shows | Blog | Support | Contact<br>2014 Company name. All right reserved Term of Use</div>
  <div class="partner">OrbitalWave</div>
</footer>

</body>
</html>
```